Truck Outfitters and Trailer Hitch Retailer Website

We are working with a hitch installer in California called Brisk Tow. They sell and install trailer hitches, bedliners for trucks, and pickup truck accessories.
Some sites to use for content/competitors:
https://www.varlomi.com/pick-up-outfitters
https://bramwells-rigs.com
https://www.thetowlodge.com
https://towlodgeinccom.quenrivsites.com
Some sites to use for inspiration:
https://www.ironmarkcouplers.com
https://quietcouplers.com
https://velmatow.com/
https://www.harborcoat.com
https://www.rugged-trailpath.com
Thank you for taking the time to consider designing a website for us. We are web developers based in Stockton, CA, USA. Most of our projects go through the same process. Understanding this process may help you win a project with us. We custom-code all of our websites in-house. We don’t have any requirements as to what tools you use for your design, but we prefer Figma files. For any design that we label as four-stars, we send it to the client for review. The client picks the final design they want us to use. Once we complete this process, we will continue to show additional clients all the four-star sites and purchase them later. Your designs will have multiple chances to sell. For better chances of success, we ask that you follow these guidelines.
IMAGES:
If you use any images or icons in the design, we ask that you have a link to the asset so we can purchase the image/icon. Most of the designs we submit do not have the customer’s images on them unless they have some great images. Be creative; show us the feeling you are trying to portray with your image choices. Use any royalty-free site you choose. We subscribe to Adobe and mainly use their images, but we can purchase images outside of Adobe.
PLEASE NOTE: we will not submit designs to clients with watermarks on the images.
FONTS:
We ask that you identify the fonts used in the design. This can be done in a message if you want. We typically use Google Fonts and Adobe Fonts.
CONTENT:
We're always open to different content and ideas. We often submit designs with stock images so the client can see our vision. We typically take pictures after the website launch to use their images with our vision. Lorem Ipsum is fine for paragraphs, but we ask that you write the headers in correct English. We want to be able to show the vision and identify the sections of the website.
INSPIRATION:
We typically add a couple of links in the brief of websites we like to help you get started in your design.
REVISIONS:
We do not often ask for revisions of the designs unless we see something in the design that may not appeal to the client. If there are slight changes that we want to make, we do that in the development process.
FEEDBACK:
We rarely give feedback on designs during the design process. We are working on many website projects and do not have the time to provide feedback. We usually respond if your request is well thought out and asks specific questions, but a note asking “feedback, please” usually goes unanswered
Number of Pages Required
1 page
Look and feel
Each slider illustrates characteristics of the customer's brand and the style your logo design should communicate.

```html
<!DOCTYPE html>
<html lang="en">
<head>
<meta charset="utf-8">
<title>Brisk Tow – Trailer Hitches &amp; Truck Outfitters</title>
<link href="https://fonts.googleapis.com/css2?family=Oswald:wght@500;600;700&family=Roboto:wght@400;500;700&family=Roboto+Condensed:wght@400;700&display=swap" rel="stylesheet">
<style>
:root{
  --red:#e50914;
  --red-deep:#d4070f;
  --ink:#000000;
  --navy:#070b18;
  --charcoal:#0e1118;
  --gray-panel:#636363;
  --text:#222;
  --muted:#777;
  --light-line:#e3e3e3;
  --pink-soft:#fde9ea;
  --white:#fff;
}
*{box-sizing:border-box;margin:0;padding:0}
html,body{width:1200px;height:3793px;overflow:hidden}
body{font-family:"Roboto",sans-serif;color:var(--text);background:var(--white);position:relative}
.abs{position:absolute}
.ph{position:absolute}

/* top bar */
.topbar{left:0;top:0;width:1200px;height:43px;background:var(--navy);color:#fff;font-size:13px}
.topbar .item{position:absolute;top:14px;display:flex;align-items:center;gap:10px}
.topbar svg{width:13px;height:13px;fill:var(--red)}

/* header */
.brand{position:absolute;display:flex;align-items:center;gap:10px;font-family:"Oswald",sans-serif;font-weight:700;font-size:24px;letter-spacing:1px}
.brand .dot{width:34px;height:34px;border-radius:50%;background:var(--red)}
.nav{left:404px;top:66px;display:flex;gap:32px;font-size:16px;color:#111}
.nav a{color:inherit;text-decoration:none;position:relative}
.nav a.active{color:var(--red)}
.nav a.active::before{content:"";position:absolute;left:-1px;right:-1px;top:-24px;height:3px;background:var(--red)}
.btn-quote{left:972px;top:59px;width:116px;height:38px;background:var(--red);color:#fff;font-family:"Oswald",sans-serif;font-weight:600;font-size:13px;display:flex;align-items:center;justify-content:center}

/* hero */
.hero-panel{left:90px;top:235px;width:415px;height:186px;background:var(--gray-panel);color:#fff;padding:24px 24px}
.hero-panel .kicker{font-family:"Oswald",sans-serif;font-weight:600;font-size:20px}
.hero-panel .title{font-family:"Oswald",sans-serif;font-weight:700;font-size:44px;line-height:1.1;text-transform:uppercase}
.btn-outline{display:inline-flex;align-items:center;justify-content:center;border:2px solid #fff;color:#fff;font-family:"Oswald",sans-serif;font-weight:600;font-size:13px;text-transform:uppercase}
.hero-panel .btn-outline{margin-top:16px;width:116px;height:38px}
.socials{left:110px;top:476px;display:flex;align-items:center;gap:10px;font-size:13px;color:#333}
.socials .c{width:33px;height:33px;border-radius:50%;border:1px solid var(--red)}
.socials .c.fill{background:var(--red)}
.slide-count{left:108px;top:578px;font-family:"Oswald",sans-serif;font-size:28px;color:var(--red)}
.slide-count span{font-family:"Roboto",sans-serif;font-size:16px;color:#222}

/* promo strip */
.promo{top:668px;width:300px;height:286px;overflow:hidden;color:#fff}
.promo p{position:absolute;left:40px;top:42px;width:235px;font-family:"Roboto Condensed",sans-serif;font-size:24px;line-height:34px}
.promo .btn-outline{position:absolute;left:40px;top:203px;width:116px;height:38px}
.promo .num{position:absolute;right:8px;bottom:-28px;font-family:"Oswald",sans-serif;font-weight:700;font-size:112px;line-height:1}

/* offer */
.sec-title{width:1200px;left:0;text-align:center;font-family:"Oswald",sans-serif;font-weight:700;font-size:46px;text-transform:uppercase;letter-spacing:.5px}
.offer{width:310px;height:258px;text-align:center}
.offer .ic{width:82px;height:82px;border-radius:50%;background:var(--pink-soft);margin:18px auto 0;display:flex;align-items:center;justify-content:center}
.offer .ic svg{width:44px;height:44px;fill:none;stroke:var(--red);stroke-width:2}
.offer h3{font-family:"Oswald",sans-serif;font-weight:600;font-size:22px;margin-top:18px;color:#111}
.offer p{font-size:13.5px;line-height:26px;color:var(--muted);margin:14px 22px 0}
.offer.featured{background:var(--ink);border-radius:6px;overflow:hidden;box-shadow:0 8px 20px rgba(0,0,0,.25)}
.offer.featured .ic{background:var(--red)}
.offer.featured .ic svg{stroke:#fff}
.offer.featured h3,.offer.featured p{color:#fff}
.corner{position:absolute;width:54px;height:54px}

/* who */
.who{left:0;top:1725px;width:1200px;height:652px;background:var(--ink);color:#fff}
.who-photo{left:112px;top:103px;width:474px;height:446px;background:linear-gradient(160deg,#7d8ea8 0%,#a8b3c2 45%,#8c8e88 70%,#5e5d57 100%);clip-path:polygon(0 0,80% 0,100% 22%,100% 100%,0 100%)}
.badge{left:68px;top:389px;width:153px;height:190px;background:var(--red);padding:18px 22px;font-family:"Oswald",sans-serif;font-weight:700}
.badge .bar{position:absolute;right:20px;top:22px;width:3px;height:146px;background:#fff}
.badge .s{font-size:16px}
.badge .big{font-size:56px;line-height:1.05}
.who-body{left:634px;top:118px;width:444px}
.who-body h2{font-family:"Oswald",sans-serif;font-weight:700;font-size:44px;text-transform:uppercase}
.who-body p{font-family:"Roboto Condensed",sans-serif;font-size:14px;line-height:25.6px;text-align:justify;margin-top:18px}
.who-body p+p{margin-top:26px}
.who-body .btn-outline{margin-top:26px;width:116px;height:38px;border-color:#fff;color:var(--red);font-size:13px}

/* features */
.features{left:0;top:2377px;width:1200px;height:467px;background:var(--red-deep);color:#fff}
.feat{top:189px;width:310px;height:175px;background:rgba(255,255,255,.12);padding:24px 28px}
.feat .row{display:flex;align-items:center;gap:10px}
.feat svg{width:38px;height:38px;fill:none;stroke:#fff;stroke-width:2;flex:none}
.feat h3{font-family:"Oswald",sans-serif;font-weight:600;font-size:21px;text-transform:uppercase;white-space:nowrap}
.feat p{font-family:"Roboto Condensed",sans-serif;font-size:13.5px;line-height:26px;margin-top:10px}

/* testimonials */
.tcard{top:3028px;height:255px;border:1px solid var(--light-line);padding:24px 24px;background:#fff}
.tcard.active{border:2px solid var(--red);box-shadow:0 6px 18px rgba(0,0,0,.12)}
.tcard .who-row{display:flex;align-items:center;gap:12px}
.avatar{width:78px;height:78px;border-radius:50%;border:3px solid var(--red);background:linear-gradient(#d9d9d9,#9a9a9a);position:relative;flex:none}
.avatar::after{content:"";position:absolute;right:-6px;bottom:-10px;width:30px;height:22px;background:var(--red);border-radius:6px 6px 14px 14px}
.tcard h4{font-family:"Oswald",sans-serif;font-weight:500;font-size:21px}
.tcard .co{font-size:13px;color:var(--muted)}
.tcard p{font-size:13px;line-height:26px;color:var(--muted);margin-top:22px}
.stars{color:#f2a516;font-size:16px;letter-spacing:3px;margin-top:4px}
.arrow{width:38px;height:38px;border-radius:50%;background:#e6e6e6;display:flex;align-items:center;justify-content:center}
.arrow svg{width:14px;height:14px;stroke:#333;stroke-width:2;fill:none}

/* footer */
.footer{left:0;top:3386px;width:1200px;height:407px;background:var(--ink);color:#fff}
.footer h5{font-family:"Oswald",sans-serif;font-weight:500;font-size:21px}
.footer ul{list-style:none;margin-top:16px;font-size:13.5px;line-height:27.5px}
.f-contact{font-size:13.5px;line-height:19px}
.f-contact .lbl{font-weight:700;font-size:12px}
.f-contact svg{width:12px;height:12px;fill:var(--red);position:absolute;left:0;top:3px}
.f-contact .ci{position:relative;padding-left:26px;margin-bottom:14px}
.f-social{display:flex;gap:11px}
.f-social .c{width:32px;height:32px;border-radius:50%;background:#fff}
.f-social .c.fill{background:var(--red)}
.f-rule{left:110px;top:331px;width:978px;height:1px;background:#333}
.copy{left:0;width:1200px;top:356px;text-align:center;font-size:14px}
.chat{left:1105px;top:296px;width:36px;height:36px;border-radius:50%;background:#fff;display:flex;align-items:center;justify-content:center}
</style>
</head>
<body>

<div class="abs topbar">
  <div class="item" style="left:108px"><svg viewBox="0 0 24 24"><path d="M6.6 10.8a15 15 0 0 0 6.6 6.6l2.2-2.2c.3-.3.7-.4 1-.2 1.1.4 2.3.6 3.6.6.6 0 1 .4 1 1V20c0 .6-.4 1-1 1A17 17 0 0 1 3 4c0-.6.4-1 1-1h3.5c.6 0 1 .4 1 1 0 1.3.2 2.5.6 3.6.1.3 0 .7-.2 1z"/></svg>+1 888 888 8888</div>
  <div class="item" style="left:481px"><svg viewBox="0 0 24 24"><path d="M12 2a7 7 0 0 0-7 7c0 5 7 13 7 13s7-8 7-13a7 7 0 0 0-7-7zm0 9.5a2.5 2.5 0 1 1 0-5 2.5 2.5 0 0 1 0 5z"/></svg>123,Lorem ipsum dolor sit amet</div>
  <div class="item" style="left:917px"><svg viewBox="0 0 24 24"><path d="M2 5h20v14H2zm2 2v.5l8 5 8-5V7z"/></svg>info@companyname.com</div>
</div>

<div class="brand" style="left:110px;top:84px;color:#111"><span class="dot"></span>BRISK TOW</div>
<nav class="abs nav">
  <a class="active" href="#">HOME</a><a href="#">ABOUT</a><a href="#">SERVICES</a><a href="#">PROJECTS</a><a href="#">BLOG</a><a href="#">CONTACT</a>
</nav>
<div class="abs btn-quote">GET A QUOTE</div>

<div class="ph" style="left:810px;top:483px;width:390px;height:185px;background:var(--red)"></div>
<div class="ph" role="img" aria-label="Couple hitching a utility trailer to a green off-road truck in a driveway" style="left:505px;top:165px;width:583px;height:399px;background:linear-gradient(135deg,#5f6b58 0%,#8b8a7c 40%,#b8a37a 70%,#6e6a60 100%)"></div>
<div class="abs hero-panel">
  <div class="kicker">WELCOME TO</div>
  <div class="title">Brisk Tow</div>
  <div class="btn-outline">Get Started</div>
</div>
<div class="abs socials">We are in Socials <span class="c"></span><span class="c"></span><span class="c fill"></span></div>
<div class="abs slide-count">1<span>/2</span></div>

<div class="abs promo" style="left:0;background:var(--red)">
  <p>Your truck should look as good as it drives, without the huge price tag.</p>
  <div class="btn-outline">Start Now</div>
  <div class="num" style="color:rgba(255,255,255,.18)">01</div>
</div>
<div class="ph" role="img" aria-label="Pickup truck towing an enclosed trailer on a tree-lined street" style="left:300px;top:668px;width:300px;height:286px;background:linear-gradient(180deg,#7a9a4e 0%,#98a87a 45%,#8f8d86 70%,#5c5b57 100%)"></div>
<div class="abs promo" style="left:600px;background:var(--charcoal)">
  <p>Find the best products on the market, spray on bedliners, protective coatings, and more.</p>
  <div class="btn-outline">Start Now</div>
  <div class="num" style="color:rgba(255,255,255,.12)">02</div>
</div>
<div class="ph" role="img" aria-label="Close-up of a trailer jack wheel and hitch coupler on grass" style="left:900px;top:668px;width:300px;height:286px;background:linear-gradient(135deg,#9fa3a6 0%,#7e8079 45%,#8a7f5c 75%,#5e5844 100%)"></div>

<h2 class="abs sec-title" style="top:1045px">What We Offer</h2>

<div class="abs offer" style="left:117px;top:1129px">
  <div class="ic"><svg viewBox="0 0 48 48"><path d="M6 30h30v-8l-5-8H13l-5 8z"/><circle cx="14" cy="32" r="3"/><circle cx="30" cy="32" r="3"/><path d="M36 16l6 3v6c0 5-6 8-6 8"/></svg></div>
  <h3>DUIS AUTE IRURE</h3>
  <p>Lorem ipsum dolor sit amet, consectetur adipiscing elit, sed do eiusmod tempor incididunt ut labore et dolore</p>
</div>
<div class="abs offer featured" style="left:445px;top:1129px">
  <svg class="corner" style="left:0;top:0" viewBox="0 0 54 54"><path d="M0 0h14L0 14z M22 0h8L0 30v-8z" fill="#e50914"/></svg>
  <svg class="corner" style="right:0;bottom:0" viewBox="0 0 54 54"><path d="M54 54H40L54 40z M32 54h-8L54 24v8z" fill="#e50914"/></svg>
  <div class="ic"><svg viewBox="0 0 48 48"><rect x="8" y="14" width="32" height="22" rx="2"/><path d="M14 14v-4h6v4M28 14v-4h6v4M25 18l-5 8h6l-3 7"/></svg></div>
  <h3>DUIS AUTE IRURE</h3>
  <p>Lorem ipsum dolor sit amet, consectetur adipiscing elit, sed do eiusmod tempor incididunt ut labore et dolore</p>
</div>
<div class="abs offer" style="left:770px;top:1129px">
  <div class="ic"><svg viewBox="0 0 48 48"><circle cx="24" cy="24" r="16"/><circle cx="24" cy="24" r="8"/><path d="M14 14l20 20M34 14L14 34"/></svg></div>
  <h3>DUIS AUTE IRURE</h3>
  <p>Lorem ipsum dolor sit amet, consectetur adipiscing elit, sed do eiusmod tempor incididunt ut labore et dolore</p>
</div>
<div class="abs offer" style="left:117px;top:1386px">
  <div class="ic"><svg viewBox="0 0 48 48"><path d="M8 32a16 16 0 1 1 32 0z"/><path d="M24 32l6-10"/><path d="M14 26h2M32 26h2M24 18v2"/></svg></div>
  <h3>DUIS AUTE IRURE</h3>
  <p>Lorem ipsum dolor sit amet, consectetur adipiscing elit, sed do eiusmod tempor incididunt ut labore et dolore</p>
</div>
<div class="abs offer" style="left:445px;top:1386px">
  <div class="ic"><svg viewBox="0 0 48 48"><circle cx="20" cy="26" r="6"/><path d="M20 14v4M20 34v4M8 26h4M28 26h4M11 17l3 3M26 32l3 3M11 35l3-3M26 20l3-3"/><circle cx="34" cy="14" r="4"/></svg></div>
  <h3>DUIS AUTE IRURE</h3>
  <p>Lorem ipsum dolor sit amet, consectetur adipiscing elit, sed do eiusmod tempor incididunt ut labore et dolore</p>
</div>
<div class="abs offer" style="left:770px;top:1386px">
  <div class="ic"><svg viewBox="0 0 48 48"><circle cx="24" cy="20" r="12"/><circle cx="24" cy="20" r="5"/><rect x="12" y="34" width="24" height="6" rx="2"/></svg></div>
  <h3>DUIS AUTE IRURE</h3>
  <p>Lorem ipsum dolor sit amet, consectetur adipiscing elit, sed do eiusmod tempor incididunt ut labore et dolore</p>
</div>

<section class="abs who">
  <div class="ph who-photo" role="img" aria-label="Pickup truck hitched to a rental moving trailer in a parking lot"></div>
  <div class="abs badge">
    <div class="bar"></div>
    <div class="s">MORE THAN</div>
    <div class="big">20</div>
    <div class="s" style="line-height:34px">YEARS OF<br>EXPERIENCE</div>
  </div>
  <div class="abs who-body">
    <h2>Who We Are</h2>
    <p>Lorem ipsum dolor sit amet, consectetur adipiscing elit, sed do eiusmod tempor incididunt ut labore et dolore magna aliqua. Ut enim ad minim veniam, quis nostrud exercitation ullamco laboris nisi ut aliquip ex ea commodo consequat. Duis aute irure dolor in reprehenderit in voluptate velit esse cillum dolore eu fugiat nulla pariatur.</p>
    <p>Excepteur sint occaecat cupidatat non proident, sunt in culpa qui officia deserunt mollit anim id est laborum. Lorem ipsum dolor sit amet, consectetur adipiscing elit, sed do eiusmod tempor incididunt ut labore et dolore magna aliqua. Ut enim ad minim veniam, quis nostrud exercitation ullamco laboris nisi ut aliquip ex ea commodo consequat.</p>
    <div class="btn-outline">Read More</div>
  </div>
</section>

<section class="abs features">
  <h2 class="abs sec-title" style="top:96px;color:#fff">Explore Features</h2>
  <div class="abs feat" style="left:112px">
    <div class="row"><svg viewBox="0 0 40 40"><path d="M6 34L22 18M10 6l8 8-4 4-8-8M26 26l8 8M30 6a6 6 0 0 0-6 8L8 30"/></svg><h3>Get A Quote</h3></div>
    <p>Lorem ipsum dolor sit amet, consectetur adip iscing elit, sed do eiusmod tempor incididunt ut labore et dolore magna aliqua.</p>
  </div>
  <div class="abs feat" style="left:445px">
    <div class="row"><svg viewBox="0 0 40 40"><rect x="5" y="8" width="24" height="26" rx="2"/><path d="M5 15h24M11 5v6M23 5v6"/><circle cx="29" cy="30" r="7"/><path d="M26 30l2 2 4-4"/></svg><h3>Book Appointment</h3></div>
    <p>Lorem ipsum dolor sit amet, consectetur adip iscing elit, sed do eiusmod tempor incididunt ut labore et dolore magna aliqua.</p>
  </div>
  <div class="abs feat" style="left:777px">
    <div class="row"><svg viewBox="0 0 40 40"><path d="M3 30h28v-6l-6-5H10l-7 5z"/><circle cx="10" cy="31" r="3"/><circle cx="25" cy="31" r="3"/><path d="M30 6l6 3v5c0 4-6 7-6 7s-6-3-6-7V9z"/></svg><h3>Weight Distribution</h3></div>
    <p>Lorem ipsum dolor sit amet, consectetur adip iscing elit, sed do eiusmod tempor incididunt ut labore et dolore magna aliqua.</p>
  </div>
</section>

<h2 class="abs sec-title" style="top:2933px">What People Say</h2>
<div class="abs arrow" style="left:35px;top:3136px"><svg viewBox="0 0 14 14"><path d="M9 2L4 7l5 5"/></svg></div>
<div class="abs arrow" style="left:1125px;top:3136px"><svg viewBox="0 0 14 14"><path d="M5 2l5 5-5 5"/></svg></div>

<div class="abs tcard" style="left:110px;width:304px">
  <div class="who-row"><div class="avatar" role="img" aria-label="Customer portrait"></div><div><h4>John Doe</h4><div class="co">Company name</div></div></div>
  <p>Lorem ipsum dolor sit amet, consectetur adipiscing elit, sed do eiusmod tempor incididunt ut labore et dolore</p>
  <div class="stars">★★★★★</div>
</div>
<div class="abs tcard active" style="left:448px;width:306px">
  <div class="who-row"><div class="avatar" role="img" aria-label="Customer portrait"></div><div><h4>John Doe</h4><div class="co">Company name</div></div></div>
  <p>Lorem ipsum dolor sit amet, consectetur adipiscing elit, sed do eiusmod tempor incididunt ut labore et dolore</p>
  <div class="stars">★★★★★</div>
</div>
<div class="abs tcard" style="left:788px;width:301px">
  <div class="who-row"><div class="avatar" role="img" aria-label="Customer portrait"></div><div><h4>John Doe</h4><div class="co">Company name</div></div></div>
  <p>Lorem ipsum dolor sit amet, consectetur adipiscing elit, sed do eiusmod tempor incididunt ut labore et dolore</p>
  <div class="stars">★★★★★</div>
</div>

<footer class="abs footer">
  <div class="brand" style="left:150px;top:140px;color:#fff;font-size:30px"><span class="dot"></span>BRISK TOW</div>
  <div class="abs f-social" style="left:204px;top:228px"><span class="c"></span><span class="c"></span><span class="c fill"></span></div>

  <div class="abs" style="left:472px;top:94px">
    <h5>Quick Links</h5>
    <ul><li>Home</li><li>About</li><li>Services</li><li>Projects</li><li>Blog</li><li>Contact</li></ul>
  </div>
  <div class="abs" style="left:644px;top:94px">
    <h5>About Company</h5>
    <ul><li>Privacy Policy</li><li>Terms of Service</li><li>Site Map</li><li>Imprint</li><li>Terms And Conditions</li></ul>
  </div>
  <div class="abs" style="left:872px;top:94px;width:190px">
    <h5>Contact Us</h5>
    <div class="f-contact" style="margin-top:18px">
      <div class="ci"><svg viewBox="0 0 24 24"><path d="M6.6 10.8a15 15 0 0 0 6.6 6.6l2.2-2.2c.3-.3.7-.4 1-.2 1.1.4 2.3.6 3.6.6.6 0 1 .4 1 1V20c0 .6-.4 1-1 1A17 17 0 0 1 3 4c0-.6.4-1 1-1h3.5c.6 0 1 .4 1 1 0 1.3.2 2.5.6 3.6.1.3 0 .7-.2 1z"/></svg><div class="lbl">Phone</div>+1 888 888 8888</div>
      <div class="ci"><svg viewBox="0 0 24 24"><path d="M2 5h20v14H2zm2 2v.5l8 5 8-5V7z"/></svg><div class="lbl">Email</div>info@companyname.com</div>
      <div class="ci"><svg viewBox="0 0 24 24"><path d="M12 2a7 7 0 0 0-7 7c0 5 7 13 7 13s7-8 7-13a7 7 0 0 0-7-7zm0 9.5a2.5 2.5 0 1 1 0-5 2.5 2.5 0 0 1 0 5z"/></svg><div class="lbl">Location</div>123,Lorem ipsum dolor sit amet, consectetur</div>
    </div>
  </div>
  <div class="abs chat"><svg viewBox="0 0 20 20" width="18" height="18"><path d="M10 3C5.6 3 2 5.9 2 9.5c0 1.8.9 3.4 2.4 4.6L4 17l3.4-1.7c.8.2 1.7.3 2.6.3 4.4 0 8-2.9 8-6.5S14.4 3 10 3z" fill="#111"/><circle cx="7" cy="9.5" r="1" fill="#fff"/><circle cx="10" cy="9.5" r="1" fill="#fff"/><circle cx="13" cy="9.5" r="1" fill="#fff"/></svg></div>
  <div class="abs f-rule"></div>
  <div class="abs copy">2024 Copyright - Company name &nbsp;| All Rights Reserved</div>
</footer>

</body>
</html>
```